Transform Your Giving

I need a tri-fold brochure that will fit in a standard number 10 business envelope. Meadowlark and Allied Services is a charitable nonprofit. The goal of this brochure is to stimulate people into thinking about other ways to make a donation. The design should communicate the essential information on donation options, create a sense of professional integrity, be graphically sharp, easy to read and laid out in a way that doesn't make the material appear crowded.

```html
<!DOCTYPE html>
<html lang="en">
<head>
<meta charset="utf-8">
<title>Transform Your Giving – Tri-fold Brochure</title>
<link href="https://fonts.googleapis.com/css2?family=Fira+Sans:ital,wght@0,300;0,400;0,500;0,600;0,700;1,600;1,700&display=swap" rel="stylesheet">
<style>
:root{
  --navy:#2c2876;
  --green:#45b649;
  --white:#ffffff;
  --ink:#2a2a3a;
  --backdrop:#7b7b7b;
}
*{box-sizing:border-box;margin:0;padding:0}
html,body{width:1096px;height:1200px;overflow:hidden;background:var(--backdrop);font-family:"Fira Sans",sans-serif;color:var(--ink)}
.spread{position:absolute;left:205px;width:687px;height:516px;display:flex;background:var(--white)}
.spread--outside{top:63px}
.spread--inside{top:621px}
.panel{position:relative;width:229px;height:516px;overflow:hidden;background:var(--white)}
.panel--navy{background:var(--navy);color:var(--white);text-align:center}
.abs{position:absolute}
.photo{position:absolute;left:0;width:229px}
.curve{position:absolute;left:0;width:229px;display:block}

/* outside left */
.impact-title{left:18px;top:222px;font-size:12.5px;font-weight:700;color:var(--navy);letter-spacing:.1px}
.impact-copy{left:18px;top:237px;width:202px;font-size:10px;line-height:12.9px;color:#222;letter-spacing:-.1px}
.checklist{left:18px;top:350px;width:200px;list-style:none;display:grid;grid-template-columns:58px 1fr;row-gap:5px;font-size:10.4px;font-weight:500;color:#222}
.checklist li{display:flex;align-items:center;gap:5px}
.tick{width:8px;height:8px;flex:none}
.brand-name{font-weight:700;color:var(--navy);text-align:center;line-height:1.15}
.brand-name--small{left:98px;top:466px;width:120px;font-size:9px}

/* outside middle */
.intro-note{left:12px;top:18px;width:205px;font-size:9.8px;line-height:12.5px;font-weight:400;letter-spacing:-.2px}
.quote{left:14px;top:102px;width:201px;font-size:10.6px;line-height:13.4px;font-weight:300}
.will-note{left:14px;top:158px;width:201px;font-size:10.2px;line-height:13.2px}
.will-note a{color:var(--green);text-decoration:underline}
.brand-name--navy{left:20px;top:240px;width:189px;font-size:13px;color:var(--white)}
.brand-dot{display:block;width:10px;height:10px;border-radius:50%;background:var(--green);margin:0 auto 6px}
.contact-title{left:0;top:318px;width:229px;font-size:11.5px;font-weight:700;text-decoration:underline;text-underline-offset:2px}
.contact-lead{left:12px;top:338px;width:205px;font-size:9.8px;line-height:13px;font-weight:500;color:var(--green);letter-spacing:-.1px}
.contact-list{left:0;top:370px;width:229px;list-style:none;font-size:8.6px;font-weight:300;letter-spacing:.3px;line-height:10.5px}
.contact-list li{display:flex;flex-direction:column;align-items:center;margin-bottom:5px}
.contact-icon{width:8px;height:8px;margin-bottom:4px}
.follow{left:0;top:489px;width:229px;display:flex;justify-content:center;align-items:center;gap:4px;font-size:8.8px;font-weight:700;text-decoration:underline}
.social-dot{width:9px;height:9px;border-radius:50%;background:var(--green);display:inline-block}

/* outside right */
.cover-title{left:0;top:14px;width:229px;text-align:center;font-size:17.5px;font-weight:600;color:var(--navy);line-height:20px}
.cover-title span{display:block;color:var(--green);font-weight:700}
.cover-sub{left:10px;top:58px;width:209px;text-align:center;font-size:8.6px;line-height:11.3px;font-weight:600;color:var(--navy)}
.option-icon{position:absolute;width:44px;height:44px}
.dots{position:absolute;height:0;border-top:1.6px dotted var(--navy)}
.option-label{position:absolute;width:80px;text-align:center;font-size:10.2px;font-weight:600;color:#222;line-height:13px;letter-spacing:.2px}
.brand-name--cover{left:20px;top:440px;width:189px;font-size:15px}

/* inside panels: each section flows, so text never stacks on text */
.section{position:absolute;left:17px;width:202px;display:flex;flex-direction:column}
.feature{display:grid;grid-template-columns:52px 1fr;column-gap:6px;align-items:start;margin-left:-2px}
.feature-icon{width:52px;height:52px;display:block}
.feature-text{padding-top:4px}
.feature-head{font-size:9.3px;line-height:11.5px;font-weight:700;color:var(--navy)}
.feature-head--lg{font-size:10.3px;line-height:12.6px}
.feature-tag{font-size:8.6px;line-height:11px;font-weight:700;font-style:italic;color:var(--green);margin-top:3px;letter-spacing:-.1px}
.copy{font-size:8.6px;line-height:10.9px;color:#2b2b2b;font-weight:400;letter-spacing:-.15px}
.copy--intro{font-size:8.9px;line-height:11.4px;font-weight:500;color:#1f1f1f;letter-spacing:-.1px}
.copy--lg{font-size:9.3px;line-height:11.8px}
.copy--md{font-size:8.8px;line-height:10.9px}
.copy--sm{font-size:8.2px;line-height:10.5px}
.copy--tight{font-size:8.8px;line-height:10.6px}
.section > .copy{margin-top:4px}
.how{font-size:10.4px;line-height:13px;font-weight:700;color:var(--navy);margin-top:6px}
.section > .how + .copy{margin-top:1px}
.bullets{list-style:none;padding-left:1px}
.bullets li{position:relative;padding-left:10px;margin-top:5px}
.bullets svg{position:absolute;left:0;top:2px;width:7px;height:7px}
.fold-shade{position:absolute;top:0;right:0;width:14px;height:516px;background:linear-gradient(90deg,rgba(0,0,0,0),rgba(0,0,0,.06))}
</style>
</head>
<body>

<!-- OUTSIDE -->
<section class="spread spread--outside">

  <!-- back-left panel -->
  <article class="panel">
    <div class="photo" style="top:0;height:225px;background:linear-gradient(160deg,#e9d9a6 0%,#c8b68a 35%,#8f8f86 70%,#6d6f6e 100%)" role="img" aria-label="Photo of a smiling young woman with her arm around an older man"></div>
    <svg class="curve" style="top:187px" width="229" height="40" viewBox="0 0 229 40" aria-hidden="true">
      <path d="M0 38 Q114 -4 229 38 L229 40 L0 40Z" fill="#fff"/>
      <path d="M0 38 Q114 -4 229 38" fill="none" stroke="#45b649" stroke-width="4"/>
    </svg>
    <div class="photo" style="top:400px;height:116px;background:linear-gradient(90deg,rgba(240,200,170,.9),rgba(250,228,210,.6) 60%,rgba(255,255,255,0))" role="img" aria-label="Close-up photo of two hands gently held together"></div>
    <h2 class="abs impact-title">THE IMPACT OF YOUR GIFT</h2>
    <p class="abs impact-copy">Your generosity drives our mission. With every Smart gift you’re supporting Meadowlark and Allied Services. Join our community of Smart Givers today and make an enduring impact. With Smart Giving your generosity reaches further. Begin your Smart Giving journey with us today.</p>
    <ul class="abs checklist">
      <li><svg class="tick" viewBox="0 0 10 10"><circle cx="5" cy="5" r="5" fill="#2c2876"/><path d="M2.6 5.2l1.6 1.6 3.2-3.3" stroke="#fff" stroke-width="1.3" fill="none"/></svg>DAFs</li>
      <li><svg class="tick" viewBox="0 0 10 10"><circle cx="5" cy="5" r="5" fill="#2c2876"/><path d="M2.6 5.2l1.6 1.6 3.2-3.3" stroke="#fff" stroke-width="1.3" fill="none"/></svg>Stocks and Securities</li>
      <li><svg class="tick" viewBox="0 0 10 10"><circle cx="5" cy="5" r="5" fill="#2c2876"/><path d="M2.6 5.2l1.6 1.6 3.2-3.3" stroke="#fff" stroke-width="1.3" fill="none"/></svg>QCDs</li>
      <li><svg class="tick" viewBox="0 0 10 10"><circle cx="5" cy="5" r="5" fill="#2c2876"/><path d="M2.6 5.2l1.6 1.6 3.2-3.3" stroke="#fff" stroke-width="1.3" fill="none"/></svg>Charitable Annuity</li>
      <li><svg class="tick" viewBox="0 0 10 10"><circle cx="5" cy="5" r="5" fill="#2c2876"/><path d="M2.6 5.2l1.6 1.6 3.2-3.3" stroke="#fff" stroke-width="1.3" fill="none"/></svg>Crypto</li>
    </ul>
    <p class="abs brand-name brand-name--small">MEADOWLARK AND ALLIED SERVICES</p>
  </article>

  <!-- back-middle panel -->
  <article class="panel panel--navy">
    <p class="abs intro-note">To learn more about Smart Giving Options and how they can benefit you and Meadowlark and Allied Services, please reach out to our team. We’re here to help you navigate these giving methods and answer any question you may have.</p>
    <p class="abs quote">Being kind to others is a way of being good to yourself.<br>Miriam Halvorsen</p>
    <p class="abs will-note">If you do not have a will, go to<br><a href="#">www.EasyWillHub.org</a><br>In 20 minutes you can have<br>a legal will – for free.</p>
    <p class="abs brand-name brand-name--navy"><span class="brand-dot"></span>MEADOWLARK AND ALLIED SERVICES</p>
    <h3 class="abs contact-title">CONTACT US</h3>
    <p class="abs contact-lead">Have more question? Please contact us at Meadowlark and Allied Services</p>
    <ul class="abs contact-list">
      <li><svg class="contact-icon" viewBox="0 0 10 10"><circle cx="5" cy="5" r="5" fill="#45b649"/><path d="M5 2.3a1.8 1.8 0 0 1 1.8 1.8C6.8 5.5 5 7.6 5 7.6S3.2 5.5 3.2 4.1A1.8 1.8 0 0 1 5 2.3z" fill="#2c2876"/></svg>1420 Prairie View Ave.<br>Suite 2 Larkton, ND 58000</li>
      <li><svg class="contact-icon" viewBox="0 0 10 10"><circle cx="5" cy="5" r="5" fill="#45b649"/><path d="M3.3 2.6l1 .2.4 1.3-.7.6a4 4 0 0 0 1.3 1.3l.6-.7 1.3.4.2 1c-2.4.5-4.6-1.7-4.1-4.1z" fill="#2c2876"/></svg>701-555-0140 (ext. 100)</li>
      <li><svg class="contact-icon" viewBox="0 0 10 10"><circle cx="5" cy="5" r="5" fill="#45b649"/><rect x="2.5" y="3.2" width="5" height="3.6" fill="#2c2876"/><path d="M2.6 3.3L5 5.2l2.4-1.9" stroke="#45b649" stroke-width=".6" fill="none"/></svg>jmorrow@meadowlarkallied.org</li>
      <li><svg class="contact-icon" viewBox="0 0 10 10"><circle cx="5" cy="5" r="5" fill="#45b649"/><circle cx="5" cy="5" r="2.6" fill="none" stroke="#2c2876" stroke-width=".8"/><path d="M2.4 5h5.2M5 2.4c-1.2 1.5-1.2 3.7 0 5.2M5 2.4c1.2 1.5 1.2 3.7 0 5.2" stroke="#2c2876" stroke-width=".6" fill="none"/></svg>www.meadowlarkallied.org</li>
    </ul>
    <p class="abs follow">FOLLOW US: <span class="social-dot"></span><span class="social-dot"></span></p>
  </article>

  <!-- front cover panel -->
  <article class="panel">
    <h1 class="abs cover-title">Transform Your Giving<span>Be Strategic, Be Smart</span></h1>
    <p class="abs cover-sub">Discover the impact of Smart Giving with Meadowlark and Allied Services</p>
    <div class="photo" style="top:88px;height:210px;background:linear-gradient(110deg,#c9cfd0 0%,#e6d8b8 45%,#f3d27c 80%,#f6c25a 100%)" role="img" aria-label="Photo of a laughing older couple embracing outdoors in sunlight"></div>
    <svg class="curve" style="top:86px" width="229" height="30" viewBox="0 0 229 30" aria-hidden="true">
      <path d="M0 26 Q114 -8 229 26 L229 0 L0 0Z" fill="#fff"/>
      <path d="M0 26 Q114 -8 229 26" fill="none" stroke="#45b649" stroke-width="3.5"/>
    </svg>
    <svg class="curve" style="top:262px" width="229" height="38" viewBox="0 0 229 38" aria-hidden="true">
      <path d="M0 34 Q114 -4 229 34 L229 38 L0 38Z" fill="#fff"/>
      <path d="M0 34 Q114 -4 229 34" fill="none" stroke="#45b649" stroke-width="3.5"/>
    </svg>

    <span class="dots" style="left:68px;top:310px;width:27px"></span>
    <span class="dots" style="left:138px;top:310px;width:24px"></span>
    <span class="dots" style="left:101px;top:370px;width:30px"></span>

    <svg class="option-icon" style="left:24px;top:287px" viewBox="0 0 44 44" role="img" aria-label="Crypto coin icon"><circle cx="22" cy="22" r="21" fill="#fff" stroke="#2c2876" stroke-width="1.5"/><circle cx="22" cy="22" r="18.5" fill="#2c2876"/><circle cx="22" cy="22" r="9" fill="none" stroke="#fff" stroke-width="1.6"/><circle cx="22" cy="22" r="5" fill="none" stroke="#fff" stroke-width="1.2"/></svg>
    <svg class="option-icon" style="left:94px;top:287px" viewBox="0 0 44 44" role="img" aria-label="Bank building icon"><circle cx="22" cy="22" r="21" fill="#fff" stroke="#2c2876" stroke-width="1.5"/><circle cx="22" cy="22" r="18.5" fill="#2c2876"/><path d="M12 17l10-6 10 6zM13 30h18M14 32h16M15 19v10M19 19v10M25 19v10M29 19v10" stroke="#fff" stroke-width="1.4" fill="none"/></svg>
    <svg class="option-icon" style="left:161px;top:287px" viewBox="0 0 44 44" role="img" aria-label="Gift box icon"><circle cx="22" cy="22" r="21" fill="#fff" stroke="#2c2876" stroke-width="1.5"/><circle cx="22" cy="22" r="18.5" fill="#2c2876"/><path d="M13 17h18v4H13zM14.5 21h15v11h-15zM22 17v15M22 17c-2-4-6-4-5-1M22 17c2-4 6-4 5-1" stroke="#fff" stroke-width="1.4" fill="none"/></svg>
    <svg class="option-icon" style="left:57px;top:347px" viewBox="0 0 44 44" role="img" aria-label="Rising bar chart icon"><circle cx="22" cy="22" r="21" fill="#fff" stroke="#2c2876" stroke-width="1.5"/><circle cx="22" cy="22" r="18.5" fill="#2c2876"/><path d="M13 31h18M14 25h3v6h-3zM20 22h3v9h-3zM26 18h3v13h-3zM13 22l6-4 4 2 8-7M27 13h4v4" stroke="#fff" stroke-width="1.3" fill="none"/></svg>
    <svg class="option-icon" style="left:130px;top:347px" viewBox="0 0 44 44" role="img" aria-label="Calendar with coin icon"><circle cx="22" cy="22" r="21" fill="#fff" stroke="#2c2876" stroke-width="1.5"/><circle cx="22" cy="22" r="18.5" fill="#2c2876"/><rect x="13" y="15" width="18" height="16" fill="none" stroke="#fff" stroke-width="1.3"/><path d="M13 19h18M17 13v4M27 13v4M16 23h3M21 23h3M26 23h3M16 27h3M21 27h3M26 27h3" stroke="#fff" stroke-width="1.2"/></svg>

    <p class="option-label" style="left:6px;top:335px">CRYPTO</p>
    <p class="option-label" style="left:76px;top:335px">DAF’S</p>
    <p class="option-label" style="left:143px;top:335px">QCDS</p>
    <p class="option-label" style="left:39px;top:396px">STOCKS &amp;<br>SECURITIES</p>
    <p class="option-label" style="left:112px;top:396px">CHARITABLE<br>ANNUITY</p>

    <p class="abs brand-name brand-name--cover"><span class="brand-dot"></span>MEADOWLARK AND ALLIED SERVICES</p>
  </article>
</section>

<!-- INSIDE -->
<section class="spread spread--inside">

  <article class="panel">
    <div class="section" style="top:16px;left:18px;width:196px">
      <p class="copy copy--intro" style="margin-top:0">We would like to introduce you to five Strategic and Smart ways to give that could potentially be more beneficial to you compared to traditional cash donations. We encourage you to keep this information as a guide for your future contributions.</p>
    </div>

    <div class="section" style="top:90px;left:18px;width:198px">
      <div class="feature">
        <svg class="feature-icon" viewBox="0 0 52 52" role="img" aria-label="Rising bar chart icon"><circle cx="26" cy="26" r="24.5" fill="#fff" stroke="#45b649" stroke-width="2.5"/><circle cx="26" cy="26" r="21" fill="#2c2876"/><path d="M15 36h22M16 29h4v7h-4zM23 25h4v11h-4zM30 20h4v16h-4zM15 25l7-5 5 2 9-8M32 14h4v4" stroke="#fff" stroke-width="1.5" fill="none"/></svg>
        <div class="feature-text">
          <h3 class="feature-head">Gifts of Stocks or Appreciated Assets Strategic &amp; Smart</h3>
          <p class="feature-tag">Consider your long-term publicly traded stock as a way to give to your favorite charity.</p>
        </div>
      </div>
      <p class="copy">You can make a significantly bigger impact when you donate long-term appreciated securities, including stock, mutual funds, &amp; bonds, directly to your favorite charity.</p>
      <h4 class="how">How Does It Work?</h4>
      <p class="copy">When you donate stock to a charity, you will generally take a tax deduction for the full market value. Because you are donating stock, your contribution &amp; tax deduction may be significantly higher than contributing the after-tax proceeds. The same benefits apply when you donate mutual funds or bonds.</p>
    </div>

    <div class="section" style="top:312px;left:18px;width:198px">
      <div class="feature">
        <svg class="feature-icon" viewBox="0 0 52 52" role="img" aria-label="Bank building icon"><circle cx="26" cy="26" r="24.5" fill="#fff" stroke="#45b649" stroke-width="2.5"/><circle cx="26" cy="26" r="21" fill="#2c2876"/><path d="M14 20l12-7 12 7zM15 35h22M16 37h20M17 22v11M22 22v11M30 22v11M35 22v11" stroke="#fff" stroke-width="1.5" fill="none"/></svg>
        <div class="feature-text">
          <h3 class="feature-head feature-head--lg">Donor-Advised Fund (DAF) Strategic &amp; Smart</h3>
          <p class="feature-tag">Consider a DAF – a simple, flexible, and tax-advantageous way to give to your favorite charities.</p>
        </div>
      </div>
      <p class="copy copy--md">A Donor-Advised Fund (DAF), is like a charitable investment account for the sole purpose of supporting your favorite charities.</p>
      <h4 class="how">How Does It Work?</h4>
      <p class="copy copy--sm">You establish a DAF &amp; contribute cash, stocks, or non-publicly traded assets, cryptocurrency, &amp; private company stock to be eligible for an immediate tax deduction. Those funds are contributed for tax-free growth. You can recommend grants be made from your DAF to any IRS qualified public charity.</p>
    </div>
    <div class="fold-shade"></div>
  </article>

  <article class="panel">
    <div class="section" style="top:15px">
      <div class="feature">
        <svg class="feature-icon" viewBox="0 0 52 52" role="img" aria-label="Gift box icon"><circle cx="26" cy="26" r="24.5" fill="#fff" stroke="#45b649" stroke-width="2.5"/><circle cx="26" cy="26" r="21" fill="#2c2876"/><path d="M15 20h22v5H15zM17 25h18v12H17zM26 20v17M26 20c-2-5-7-5-6-1M26 20c2-5 7-5 6-1" stroke="#fff" stroke-width="1.5" fill="none"/></svg>
        <div class="feature-text">
          <h3 class="feature-head" style="font-size:8.8px;line-height:11px">Qualified Charitable Distributions (QCDs) Strategic &amp; Smart</h3>
          <p class="feature-tag" style="margin-top:2px">Consider a QCD – when planning your IRA withdrawal strategy… &amp; donate to your favorite charity.</p>
        </div>
      </div>
      <p class="copy copy--md">IRA owners at age 70 ½ or over can transfer dollars from their IRA to charity tax-free each year. These transfers known as Qualified Charitable Distributions (QCDs) offer eligible older Americans a great way to easily give to charity.</p>
      <h4 class="how">How Does It Work?</h4>
      <p class="copy copy--md">Are you 72 and required to take a minimum distribution (RMD) from your IRA but do not need the funds? Consider a Qualified Charitable Distribution. Normally, distributions from a traditional IRA are taxable when received. With a QCD, these distributions become tax-free when paid directly from the IRA to your favorite eligible charity. An IRA owner wishing to make a QCD should contact their IRA trustee, allowing time to complete the transaction before the end of the year to receive the tax benefit.</p>
    </div>

    <div class="section" style="top:290px">
      <div class="feature">
        <svg class="feature-icon" viewBox="0 0 52 52" role="img" aria-label="Calendar with coin icon"><circle cx="26" cy="26" r="24.5" fill="#fff" stroke="#45b649" stroke-width="2.5"/><circle cx="26" cy="26" r="21" fill="#2c2876"/><rect x="15" y="18" width="22" height="19" fill="none" stroke="#fff" stroke-width="1.4"/><path d="M15 23h22M20 15v5M32 15v5M18 27h4M24 27h4M30 27h4M18 32h4M24 32h4M30 32h4" stroke="#fff" stroke-width="1.3"/></svg>
        <div class="feature-text">
          <h3 class="feature-head">Charitable Gift Annuity<br>Strategic &amp; Smart</h3>
          <p class="feature-tag">Consider establishing a<br>Charitable Gift Annuity</p>
        </div>
      </div>
      <p class="copy copy--tight">You make a donation to a single charity. The gift is set aside in a reserve account and invested.</p>
      <h4 class="how" style="margin-top:3px">How Does It Work?</h4>
      <p class="copy copy--tight">A charitable gift annuity is a contract between a donor &amp; a charity. As a donor, you make a sizable gift to charity using cash, securities, or possibly other assets. This money is then invested. In return, you become eligible to take a partial tax deduction for your donation, plus you receive a fixed stream of income from the charity for the rest of your life. At the end of your life (as well as your spouse’s, if you’re giving as a couple), the charity receives the remainder of the gift.</p>
    </div>
  </article>

  <article class="panel">
    <div class="section" style="top:15px;left:16px">
      <div class="feature">
        <svg class="feature-icon" viewBox="0 0 52 52" role="img" aria-label="Crypto coin icon"><circle cx="26" cy="26" r="24.5" fill="#fff" stroke="#45b649" stroke-width="2.5"/><circle cx="26" cy="26" r="21" fill="#2c2876"/><circle cx="26" cy="26" r="11" fill="none" stroke="#fff" stroke-width="1.8"/><circle cx="26" cy="26" r="6" fill="none" stroke="#fff" stroke-width="1.3"/></svg>
        <div class="feature-text">
          <h3 class="feature-head feature-head--lg">Cryptocurrency<br>Strategic &amp; Smart</h3>
          <p class="feature-tag" style="font-size:8.7px">Consider donating Coinmark and other cryptocurrencies to your favorite charity.</p>
        </div>
      </div>
      <p class="copy copy--lg">Coinmark and other cryptocurrencies can be donated to charity just like other appreciated assets such as stocks and other business interests. Before you sell coins &amp; donate the after-tax proceeds, consider donating your coins directly to a favorite charity.</p>
      <h4 class="how" style="margin-top:7px">How Does It Work?</h4>
      <p class="copy">Many donors find it useful to open a Donor-Advised Fund (DAF). This strategy includes two significant benefits, both for you and your favorite charity.</p>
      <ul class="copy bullets" style="margin-top:2px">
        <li><svg viewBox="0 0 10 10"><circle cx="5" cy="5" r="5" fill="#2c2876"/><path d="M2.6 5.2l1.6 1.6 3.2-3.3" stroke="#fff" stroke-width="1.3" fill="none"/></svg>Your tax deduction will be equal to the fair market value of the donated coins (as determined by a qualified appraisal).</li>
        <li><svg viewBox="0 0 10 10"><circle cx="5" cy="5" r="5" fill="#2c2876"/><path d="M2.6 5.2l1.6 1.6 3.2-3.3" stroke="#fff" stroke-width="1.3" fill="none"/></svg>Your cryptocurrency donation is tax-smart because it may eliminate capital gains taxes on the value / appreciation AND your favorite charity will receive 100% of the value of the contribution.</li>
      </ul>
      <p class="copy" style="margin-top:7px">Often charities are not able to accept direct donations of coins/crypto so using a DAF is a great way to donate these assets.</p>
    </div>
    <div class="photo" style="top:368px;height:148px;background:linear-gradient(100deg,#3f4a3c 0%,#8a7a6a 40%,#d8b8a0 70%,#7a6a5a 100%)" role="img" aria-label="Photo of an older man and a young woman smiling together"></div>
    <svg class="curve" style="top:362px" width="229" height="28" viewBox="0 0 229 28" aria-hidden="true">
      <path d="M0 24 Q114 -6 229 24 L229 0 L0 0Z" fill="#fff"/>
      <path d="M0 24 Q114 -6 229 24" fill="none" stroke="#45b649" stroke-width="3.5"/>
    </svg>
  </article>
</section>

</body>
</html>
```